Brightfen Business Card Redesign & Logo Update

We need to update our business cards to something more modern and fresh. Brightfen can provide the current color schemes and old design examples, but welcome creativity in helping us with this redesign. PLEASE NOTE that we no longer utilize the "tree" and/or "leaf" imagery in our branding. If able would apprecaite an update on the quality of our "words only" logo in Ai. / PNG formats too.

Target Market(s)

Investors, landowners, corporate partners, contractors

Industry/Entity Type

Environmental Restoration & Conservation

Contact Information for Business Card

Logo, persons name, title, mailing address, phone and email, website url

Font styles to use
Other font styles liked:
• Merriweather

Requirements
Nice to have
• Logo, persons name, title, mailing address, phone and email, website url, but open to ideams
Should not have
• No all back backgrounds

```html
<!DOCTYPE html>
<html lang="en">
<head>
<meta charset="utf-8">
<title>Brightfen Business Card</title>
<link href="https://fonts.googleapis.com/css2?family=Open+Sans:wght@400;600;700&display=swap" rel="stylesheet">
<style>
  :root {
    --backdrop: #3b3b3b;
    --card-white: #ffffff;
    --brand-green: #177a3c;
    --brand-green-deep: #11612f;
    --brand-orange: #ea7a22;
    --ink-dark: #1d1d1d;
    --ink-grey: #6b6b6b;
    --ink-light: #ffffff;
  }
  * { box-sizing: border-box; margin: 0; padding: 0; }
  html, body {
    width: 1200px; height: 801px; overflow: hidden;
    background: var(--backdrop);
    font-family: "Open Sans", sans-serif;
  }
  .sheet {
    position: relative; width: 1200px; height: 801px;
    display: flex; align-items: center; justify-content: center; gap: 50px;
  }
  .card {
    position: relative; width: 520px; height: 300px;
    border-radius: 16px; overflow: hidden;
  }
  .wordmark__name {
    font-family: "Open Sans", sans-serif; font-weight: 700;
    font-size: 54px; line-height: 1.05; letter-spacing: 1px;
    color: var(--brand-green);
  }
  .wordmark__tagline {
    font-family: "Open Sans", sans-serif; font-weight: 600;
    font-size: 14px; letter-spacing: 1.2px; margin-top: 6px;
    color: var(--ink-dark);
  }
  /* Front */
  .card--front { background: var(--card-white); }
  .card--front .wordmark { position: absolute; left: 70px; top: 46px; }
  .person {
    position: absolute; left: 70px; top: 178px; text-align: right; width: 170px;
  }
  .person__name {
    font-weight: 700; font-size: 17px; color: var(--brand-green); letter-spacing: 0.5px;
  }
  .person__title { font-size: 14px; color: var(--ink-grey); }
  .divider {
    position: absolute; left: 262px; top: 168px; width: 1px; height: 56px;
    background: var(--brand-green);
  }
  .contact {
    position: absolute; left: 282px; top: 166px; list-style: none;
    font-size: 13px; color: var(--ink-grey); line-height: 20px;
  }
  .contact li { display: flex; align-items: center; gap: 7px; }
  .contact svg { width: 11px; height: 11px; fill: var(--brand-orange); }
  .address-band {
    position: absolute; left: 0; right: 0; bottom: 14px; height: 34px;
    background: var(--brand-green); color: var(--ink-light);
    font-size: 14px; display: flex; align-items: center; padding-left: 70px;
  }
  /* Back */
  .card--back {
    background: linear-gradient(135deg, var(--brand-green), var(--brand-green-deep));
    display: flex; align-items: center; justify-content: center;
  }
  .card--back .wordmark__name { font-size: 66px; color: var(--ink-light); }
  .card--back .wordmark__tagline { font-size: 17px; color: var(--ink-light); }
  .back-rule {
    position: absolute; left: 0; right: 0; bottom: 14px; height: 6px;
    background: var(--brand-orange);
  }
</style>
</head>
<body>
  <main class="sheet">
    <section class="card card--front" aria-label="Business card front">
      <div class="wordmark">
        <div class="wordmark__name">BRIGHTFEN</div>
        <div class="wordmark__tagline">ENVIRONMENTAL CREDIT COMPANY</div>
      </div>
      <div class="person">
        <div class="person__name">DORIAN KESSLER</div>
        <div class="person__title">President</div>
      </div>
      <div class="divider"></div>
      <ul class="contact">
        <li><svg viewBox="0 0 10 10" aria-hidden="true"><path d="M2 0.5 L3.6 2.6 L2.8 3.6 Q4 6 6.4 7.2 L7.4 6.4 L9.5 8 L8.4 9.5 Q2.5 8.8 0.5 1.6 Z"/></svg>555-318-4702</li>
        <li><svg viewBox="0 0 10 10" aria-hidden="true"><path d="M0 2 H10 V8.5 H0 Z M0 2 L5 5.6 L10 2" stroke="#fff" stroke-width="0.8"/></svg>dkessler@brightfen.com</li>
        <li><svg viewBox="0 0 10 10" aria-hidden="true"><circle cx="5" cy="5" r="4.6"/></svg>www.brightfen.com</li>
      </ul>
      <div class="address-band">4820 Marlow Bay Dr, Seacliff CA 92010</div>
    </section>

    <section class="card card--back" aria-label="Business card back">
      <div class="wordmark">
        <div class="wordmark__name">BRIGHTFEN</div>
        <div class="wordmark__tagline">ENVIRONMENTAL CREDIT COMPANY</div>
      </div>
      <div class="back-rule"></div>
    </section>
  </main>
</body>
</html>
```